Brookvale Building Company - advertisement poster

I am looking to print some canvas signs to advertise my general contracting company, Brookvale Building Company. The sign will measure 6' long x 3' high so the size should match that ratio. I already have a logo icon, which is the Letter 'B' and some trees that I would like to incorporate, see attached. I would also like the to have the following information listed:
1) phone number: 831-555-0172
2) email: brookvalebuildingcompany@mailnest.example
3) website: brookvalebuildingcompany.example
4) Lic#4826130
5) I want to use this text: "BUILD WITH THE B-CREW!"

The ad should be relatively simple and clean. Black and Green are my company colors. I am open to creative ideas!

Target Market(s)

People looking to renovate their homes

Industry/Entity Type

Construction

Colors
59FF00
82FF00
B8FF75
E3FFCB
F4FFEA

Requirements
Must have
• Must have my company logo
Should not have
• No photos or complex graphics

```html
<!DOCTYPE html>
<html lang="en">
<head>
<meta charset="utf-8">
<title>Brookvale Building Company – Sign</title>
<link rel="stylesheet" href="https://fonts.googleapis.com/css2?family=Bebas+Neue&family=Montserrat:wght@400;700;800&display=swap">
<style>
  :root {
    --backdrop: #ededed;
    --ink: #000000;
    --paper: #ffffff;
    --green: #72b646;
    --green-light: #9fd878;
    --band-grey: #8e8e8e;
    --tool-tone: #1a1a1a;
  }
  html, body {
    margin: 0;
    padding: 0;
    width: 1200px;
    height: 699px;
    overflow: hidden;
    background: var(--backdrop);
  }
  .sign {
    display: block;
    width: 1200px;
    height: 699px;
  }
  .sign-face { fill: var(--paper); filter: drop-shadow(0 2px 4px rgba(0,0,0,.18)); }
  .panel-dark { fill: var(--ink); }
  .band-grey { fill: var(--band-grey); }
  .house-body { fill: var(--green); }
  .house-highlight { fill: var(--green-light); }
  .tool-area { fill: var(--tool-tone); }
  .logo-square { fill: var(--green); }
  .logo-square--light { fill: var(--paper); }
  .est-text {
    font-family: "Montserrat", sans-serif;
    font-weight: 400;
    font-size: 22px;
    fill: var(--paper);
  }
  .est-rule { stroke: var(--green); stroke-width: 2.5; }
  .brand-name {
    font-family: "Montserrat", sans-serif;
    font-weight: 700;
    fill: var(--paper);
  }
  .brand-name--main { font-size: 88px; }
  .brand-name--sub { font-size: 36px; }
  .license-frame { fill: none; stroke: var(--green); stroke-width: 7; }
  .license-text {
    font-family: "Montserrat", sans-serif;
    font-weight: 400;
    font-size: 48px;
    fill: var(--paper);
  }
  .headline { font-family: "Bebas Neue", sans-serif; }
  .headline--build { font-size: 232px; fill: var(--paper); }
  .headline--small { font-size: 108px; fill: var(--ink); }
  .headline--crew { font-size: 212px; fill: var(--ink); }
  .icon-ring { fill: none; stroke: var(--green); stroke-width: 6; }
  .icon-glyph { fill: var(--paper); }
  .icon-wave { fill: none; stroke: var(--paper); stroke-width: 8; stroke-linecap: round; }
  .icon-line { fill: none; stroke: var(--ink); stroke-width: 2.5; }
  .phone-number {
    font-family: "Montserrat", sans-serif;
    font-weight: 800;
    font-size: 150px;
    fill: var(--paper);
  }
  .contact-text {
    font-family: "Montserrat", sans-serif;
    font-weight: 700;
    font-size: 25px;
    fill: var(--paper);
  }
  .contact-rule { stroke: var(--green); stroke-width: 4; }
</style>
</head>
<body>
<svg class="sign" viewBox="0 0 2520 1468" xmlns="http://www.w3.org/2000/svg" role="img" aria-label="Brookvale Building Company sign: Build with the B-Crew">
  <rect class="sign-face" x="148" y="169" width="2225" height="1130"/>

  <!-- left dark arrow panel -->
  <polygon class="panel-dark" points="148,169 430,169 1102,735 430,1299 148,1299"/>
  <polygon class="band-grey" points="1083,752 1111,775 490,1299 430,1299"/>

  <!-- house shape -->
  <g class="house">
    <polygon class="house-body" points="1127,538 1725,305 2325,538 2185,538 2185,893 1267,893 1267,538"/>
    <polygon class="house-highlight" points="1695,317 1725,305 2325,538 2260,538"/>
    <rect class="house-highlight" x="2133" y="538" width="52" height="355"/>
  </g>

  <!-- hammer illustration area -->
  <rect class="tool-area" x="1608" y="366" width="190" height="101" rx="14" role="img" aria-label="Hammer illustration"/>

  <!-- headline -->
  <g class="headline-group">
    <text class="headline headline--build" x="1438" y="658" textLength="386" lengthAdjust="spacingAndGlyphs">BUILD</text>
    <text class="headline headline--small" x="1853" y="573" textLength="158" lengthAdjust="spacingAndGlyphs">WITH</text>
    <text class="headline headline--small" x="1853" y="658" textLength="118" lengthAdjust="spacingAndGlyphs">THE</text>
    <rect class="logo-square--light" x="1440" y="712" width="118" height="118"/>
    <text class="headline headline--crew" x="1590" y="832" textLength="520" lengthAdjust="spacingAndGlyphs">B-CREW!</text>
  </g>

  <!-- brand block -->
  <g class="brand">
    <rect class="logo-square" x="489" y="578" width="120" height="120"/>
    <line class="est-rule" x1="255" y1="639" x2="348" y2="639"/>
    <text class="est-text" x="302" y="667" text-anchor="middle" textLength="108" lengthAdjust="spacingAndGlyphs">ESTD</text>
    <line class="est-rule" x1="255" y1="679" x2="348" y2="679"/>
    <line class="est-rule" x1="746" y1="639" x2="839" y2="639"/>
    <text class="est-text" x="792" y="667" text-anchor="middle" textLength="107" lengthAdjust="spacingAndGlyphs">2020</text>
    <line class="est-rule" x1="746" y1="679" x2="839" y2="679"/>
    <text class="brand-name brand-name--main" x="548" y="800" text-anchor="middle" textLength="644" lengthAdjust="spacingAndGlyphs">BROOKVALE</text>
    <text class="brand-name brand-name--sub" x="549" y="843" text-anchor="middle" textLength="640" lengthAdjust="spacingAndGlyphs">BUILDING COMPANY</text>
    <rect class="license-frame" x="382" y="876" width="334" height="79" rx="38"/>
    <text class="license-text" x="549" y="932" text-anchor="middle" textLength="272" lengthAdjust="spacingAndGlyphs">LIC#4826130</text>
  </g>

  <!-- contact band -->
  <polygon class="panel-dark" points="1054,893 2373,893 2373,1299 597,1299"/>

  <g class="contact-phone">
    <circle class="icon-ring" cx="1233" cy="1033" r="103"/>
    <path class="icon-glyph" transform="translate(1168,984) scale(4.8)" d="M6.62 10.79c1.44 2.83 3.76 5.14 6.59 6.59l2.2-2.2c.27-.27.67-.36 1.02-.24 1.12.37 2.33.57 3.57.57.55 0 1 .45 1 1V20c0 .55-.45 1-1 1-9.39 0-17-7.61-17-17 0-.55.45-1 1-1h3.5c.55 0 1 .45 1 1 0 1.25.2 2.45.57 3.57.11.35.03.74-.25 1.02l-2.2 2.2z"/>
    <path class="icon-wave" d="M1241,1013 a16,16 0 0 1 16,16"/>
    <path class="icon-wave" d="M1245,995 a34,34 0 0 1 34,34"/>
    <text class="phone-number" x="1393" y="1085" textLength="922" lengthAdjust="spacingAndGlyphs">831-555-0172</text>
  </g>

  <g class="contact-web">
    <circle class="icon-ring" cx="897" cy="1199" r="33"/>
    <circle class="icon-glyph" cx="897" cy="1199" r="20"/>
    <ellipse class="icon-line" cx="897" cy="1199" rx="8" ry="18"/>
    <line class="icon-line" x1="879" y1="1199" x2="915" y2="1199"/>
    <text class="contact-text" x="965" y="1208" textLength="539" lengthAdjust="spacingAndGlyphs">BROOKVALEBUILDINGCOMPANY.EXAMPLE</text>
    <line class="contact-rule" x1="965" y1="1219" x2="1504" y2="1219"/>
  </g>

  <g class="contact-email">
    <circle class="icon-ring" cx="1594" cy="1199" r="33"/>
    <circle class="icon-glyph" cx="1594" cy="1199" r="20"/>
    <rect class="icon-line" x="1583" y="1192" width="22" height="15"/>
    <polyline class="icon-line" points="1583,1192 1594,1201 1605,1192"/>
    <text class="contact-text" x="1659" y="1208" textLength="661" lengthAdjust="spacingAndGlyphs">BROOKVALEBUILDINGCOMPANY@MAILNEST.EXAMPLE</text>
    <line class="contact-rule" x1="1659" y1="1219" x2="2320" y2="1219"/>
  </g>
</svg>
</body>
</html>
```